New Website Announcement

We need a flyer to announce our new website to customers and prospective clients. The website will be launching soon, but I can provide a detailed outline in PDF form with copy and imagery to serve as inspiration for this design.

I would like a postcard size document that can be mailed in an envelope (no need for postcard style mailer info on 1 side)

About my company:

Verity Lane Studio is a new breed of marketing consulting agency built for the next frontier of consumer learning. Social interaction will be at the heart of great insights going forward – in how consumers engage with brands and in how organizations socialize what they learn to gain competitive advantage.
By fusing innovative insights techniques, technology and compelling graphic design-based reporting, we ensure results get noticed and make an impact.

contact info that can also be included:

Email: marek@veritylane-studio.net

Phone: 518-732-5164

Thanks

Attention all designers submitting a design for this project. Please keep in mind a few important details about this project.

1. Remember that the main objective of this postcard is to announce my new website.

2. Please be sure to read the brief for the copy I would like on each side. You can be creative in how it is displayed, but I need this key information somewhere. All other copy on the attached files is for your background only.

3. Please do not submit overly simple designs that just take the images I provided and overlay a text box with my copy. I could easily do this myself in PowerPoint in 5 minutes.

4. Remember that the design should be edgy and modern but needs to be professional and speak to a business audience.

Please submit any questions. Thank you for your submissions. 

Marek

Target Market(s)

senior level marketing and research clients at large companies and agencies

Industry/Entity Type

Marketing

Requirements
Must have
• Main message:

Need an engaging way to tell customers and prospective clients that we have a new website and that they should come visit us online to learn more about out services, check out case studies and read about our exciting partnerships.

COPY TO USE - UPDATED

Side 1:
(logo)
Introducing Verity Lane Studio

Let’s talk about taking research out of the dark ages.

Visit our newly launched website to learn how and get in touch.

www.veritylane-studio.net

Side 2
Logo
followed by tagline:
Consumer insights that get noticed.
A leading-edge marketing partnership that really works.

Additional text to use on Side 2:
How we can help...

Think of us as your go-to resource for identifying and incorporating the most innovative and exciting techniques into your research programs. We carefully curate and develop close partnerships with the best of the best - from online qualitative research and mobile ethnography to social media listening and fresh takes on concept testing, we can guide the way.

Plus, we believe that socializing consumer learning is just as critical as gathering it.By taking insights deliverables to the next level – through infographics, videos, magazines,interactive profiles and so much more – we are getting stakeholders excited to engage with research and inspired to take action because of it.
It’s a new way to look at insights from a new type of partner. And, it’s a new way to get the most from your research dollars.
Nice to have
• could incorporate our website main image of the lamp on white brick background which is attached, but not 100% mandatory.
Should not have
• - should not be too playful or young, but needs to be modern and design focused

- should not be cluttered or overly 'salesy'

- needs to be upscale and elegant / compelling and aligned with the look and feel of the website imagery (see attached)

```html
<!DOCTYPE html>
<html lang="en">
<head>
<meta charset="utf-8">
<title>Verity Lane Studio – New Website Postcard</title>
<link rel="stylesheet" href="https://fonts.googleapis.com/css2?family=Fira+Sans+Extra+Condensed:wght@400;500;600;700&family=Open+Sans:wght@400&display=swap">
<style>
  :root {
    --blue: #2f7ac3;
    --ink: #111111;
    --bar: #0c0c0c;
    --paper: #ffffff;
    --stage: #ffffff;
    --text: #333333;
    --brick-light: #f1f1ef;
    --brick-mid: #cfcfcc;
    --brick-dark: #8f8f8c;
  }
  * { margin: 0; padding: 0; box-sizing: border-box; }
  html, body { width: 1200px; height: 449px; overflow: hidden; background: var(--stage); }
  body { position: relative; font-family: "Open Sans", sans-serif; }

  .card {
    position: absolute; background: var(--paper); overflow: hidden;
    box-shadow: 0 3px 9px rgba(0,0,0,.35);
  }
  .card--front { left: 33px; top: 33px; width: 533px; height: 383px; }
  .card--back { left: 632px; top: 33px; width: 536px; height: 383px; }

  .condensed { font-family: "Fira Sans Extra Condensed", sans-serif; }

  .icon-badge {
    position: absolute; width: 44px; height: 44px; border-radius: 50%;
    background: var(--blue); border: 3px solid #fff;
    box-shadow: 0 2px 4px rgba(0,0,0,.4);
    display: flex; align-items: center; justify-content: center;
  }

  /* Front */
  .hero-photo {
    position: absolute; left: 40px; top: 29px; width: 455px; height: 315px;
    background:
      radial-gradient(ellipse 40% 30% at 42% 32%, rgba(255,255,255,.95), rgba(255,255,255,0) 70%),
      linear-gradient(180deg, var(--brick-mid) 0%, var(--brick-light) 30%, var(--brick-light) 62%, var(--brick-mid) 80%, var(--brick-dark) 100%);
  }
  .announce-bar {
    position: absolute; left: 29px; top: 35px; width: 470px; height: 40px;
    background: linear-gradient(180deg, #2a2a2a, var(--bar) 50%);
    color: #fff; font-weight: 600; font-size: 14px; line-height: 16px;
    padding: 4px 0 0 40px; white-space: nowrap;
  }
  .announce-bar .icon-badge { left: 0; top: -1px; width: 42px; height: 42px; }
  .url-ribbon {
    position: absolute; left: 366px; top: 72px; width: 175px; height: 28px;
    background: var(--blue); color: #fff; font-weight: 600; font-size: 14.5px;
    line-height: 28px; text-align: center; transform: rotate(52deg);
    box-shadow: 0 2px 4px rgba(0,0,0,.35); white-space: nowrap;
  }
  .front-wordmark {
    position: absolute; left: 130px; top: 170px; width: 200px;
    font-weight: 700; color: var(--blue);
    font-size: 40px; line-height: 42px; text-transform: uppercase; text-align: center;
  }
  .front-contact {
    position: absolute; right: 53px; top: 310px; text-align: right;
    font-size: 11px; line-height: 16px; color: var(--ink);
  }
  .front-contact span { display: inline-flex; align-items: center; gap: 4px; }

  /* Back */
  .back-wordmark {
    position: absolute; left: 41px; top: 37px; width: 130px;
    font-weight: 700; color: var(--blue);
    font-size: 25px; line-height: 26px; text-transform: uppercase;
  }
  .tagline {
    position: absolute; left: 184px; top: 36px;
    font-weight: 600; color: var(--blue);
    font-size: 15px; line-height: 20px; white-space: nowrap;
  }
  .help-bar {
    position: absolute; left: 68px; top: 110px; width: 437px; height: 25px;
    background: linear-gradient(180deg, #2a2a2a, var(--bar) 55%);
    color: #fff; font-weight: 600; font-size: 20px; line-height: 25px; padding-left: 20px;
    box-shadow: 0 2px 3px rgba(0,0,0,.3);
  }
  .help-bar .icon-badge { left: -30px; top: -9px; }
  .help-copy {
    position: absolute; left: 88px; top: 141px; width: 410px;
    font-size: 8.1px; line-height: 10.6px; color: var(--text);
  }
  .focus-title {
    position: absolute; left: 89px; top: 264px;
    font-weight: 600; color: var(--blue); font-size: 20px; line-height: 26px;
  }
  .focus-list { list-style: none; }
  .focus-item {
    position: absolute; top: 294px; width: 110px;
    display: flex; flex-direction: column; align-items: center;
  }
  .focus-item:nth-child(1) { left: 75px; }
  .focus-item:nth-child(2) { left: 183px; }
  .focus-item:nth-child(3) { left: 290px; }
  .focus-item:nth-child(4) { left: 393px; }
  .focus-item .icon-badge { position: static; width: 42px; height: 42px; }
  .focus-item p {
    margin-top: 6px; font-weight: 400; font-size: 9.5px; line-height: 12px;
    color: var(--ink); white-space: nowrap;
  }
</style>
</head>
<body>

<section class="card card--front">
  <div class="hero-photo" role="img" aria-label="Photo of a black arc floor lamp glowing against a whitewashed brick wall"></div>

  <div class="announce-bar condensed">
    <span class="icon-badge">
      <svg width="18" height="18" viewBox="0 0 20 20"><path d="M5 2 L5 16 L8.5 12.5 L11 18 L13 17 L10.5 11.5 L15 11.5 Z" fill="#fff"/></svg>
    </span>
    Let’s talk about taking research out of the dark ages.<br>
    Visit our newly launched website to learn how and get in touch.
  </div>

  <div class="url-ribbon condensed">www.veritylane-studio.net</div>

  <div class="front-wordmark condensed">Verity Lane<br>Studio</div>

  <div class="front-contact">
    <span><svg width="12" height="9" viewBox="0 0 12 9"><rect x=".5" y=".5" width="11" height="8" fill="none" stroke="#111"/><path d="M.5 .5 L6 5 L11.5 .5" fill="none" stroke="#111"/></svg>marek@veritylane-studio.net</span><br>
    <span><svg width="10" height="10" viewBox="0 0 10 10"><path d="M2 0.5 L4 2.8 L3 4 Q4.5 6 6 7 L7.2 6 L9.5 8 L8 9.6 Q3.5 9 0.4 2 Z" fill="#111"/></svg>518-732-5164</span>
  </div>
</section>

<section class="card card--back">
  <div class="back-wordmark condensed">Verity Lane<br>Studio</div>
  <div class="tagline condensed">Consumer insights that get noticed.<br>A leading-edge marketing partnership that really works</div>

  <div class="help-bar condensed">
    <span class="icon-badge">
      <svg width="22" height="22" viewBox="0 0 22 22" fill="none" stroke="#fff" stroke-width="1.6"><circle cx="11" cy="10" r="4.5"/><path d="M9 15.5h4M9.5 18h3M11 1.5v2M3 10h-2M21 10h-2M5 4l-1.4-1.4M17 4l1.4-1.4"/></svg>
    </span>
    How we can help...
  </div>

  <div class="help-copy">
    Think of us as your go-to resource for identifying and incorporating the most innovative and exciting techniques into your research programs. We carefully curate and develop close partnerships with the best of the best - from online qualitative research and mobile ethnography to social media listening and fresh takes on concept testing, we can guide the way.<br>
    Plus, we believe that socializing consumer learning is just as critical as gathering it. By taking insights deliverables to the next level – through infographics, videos, magazines, interactive profiles and so much more – we are getting stakeholders excited to engage with research and inspired to take action because of it.<br>
    It’s a new way to look at insights from a new type of partner. And, it’s a new way to get the most from your research dollars.
  </div>

  <div class="focus-title condensed">We focus on designing the…</div>

  <ul class="focus-list">
    <li class="focus-item">
      <span class="icon-badge"><svg width="22" height="22" viewBox="0 0 22 22" fill="none" stroke="#fff" stroke-width="2"><circle cx="9" cy="9" r="5.5"/><path d="M13 13l6 6" stroke-linecap="round"/></svg></span>
      <p class="condensed">best research approach</p>
    </li>
    <li class="focus-item">
      <span class="icon-badge"><svg width="24" height="22" viewBox="0 0 24 22" fill="none" stroke="#fff" stroke-width="1.8" stroke-linejoin="round"><path d="M1 8l5-3 5 2 5-2 5 3M3 9l7 7 2-1 2 1 6-7"/><path d="M9 11l3 3M12 10l3 3"/></svg></span>
      <p class="condensed">most flexible partnership</p>
    </li>
    <li class="focus-item">
      <span class="icon-badge"><svg width="22" height="22" viewBox="0 0 22 22" fill="#fff"><rect x="3" y="12" width="3" height="7"/><rect x="8" y="9" width="3" height="10"/><rect x="13" y="11" width="3" height="8"/><rect x="18" y="6" width="2" height="13"/><path d="M3 9l5-4 5 3 6-5" fill="none" stroke="#fff" stroke-width="1.5"/></svg></span>
      <p class="condensed">most impactful analysis</p>
    </li>
    <li class="focus-item">
      <span class="icon-badge"><svg width="22" height="22" viewBox="0 0 22 22" fill="none" stroke="#fff" stroke-width="1.6"><rect x="2" y="3" width="18" height="15" rx="1.5"/><path d="M2 6.5h18"/><path d="M11 15.5l-3.5-3.3a2 2 0 0 1 3.5-2 2 2 0 0 1 3.5 2z" fill="#fff" stroke="none"/></svg></span>
      <p class="condensed">most elegant deliverables</p>
    </li>
  </ul>
</section>

</body>
</html>
```